Human Resource Consulting practice needs a business card design

We need a business card design (double sided colour) for our Human Resource (HR) consulting practice in regional New South Wales, australia. Our business name is Staff Compass. We support small and medium business across the Mid North Coast of New South Wales by providing them with outsourced HR support, services and products to help them achieve compliance with workplace legislation and across all areas of the employment lifecycle from recruitment to termination and everything in between. Our corporate colours are hot pink and black. The final design should communicate professionalism, trust, people focus.
I have attached the current (old) business card for your reference.

Target Market(s)

Business owners and high level managers

Industry/Entity Type

Business

Contact Information for Business Card

Name
Title
Phone no
Mobile no
Address
PO Box
email address
website

Colors
e34197

Requirements
Must have
• Tempate for changing business card personal details including Name, position title, mobile number, email address.
• Keep current logo and colours as per attached
• Logo must be presented in 2 colours or black only not white
Nice to have
• One side logo and graphic only other side logo and personal details
Should not have
• Should not be the same as the current version (attached) but a modern interpretation.
• Does not need a busy reverse side with our list of services as per current version. I feel this is too busy.
• No photos

```html
<!DOCTYPE html>
<html lang="en">
<head>
<meta charset="utf-8">
<title>Staff Compass – Business Card</title>
<link href="https://fonts.googleapis.com/css2?family=Montserrat:wght@400;500;600;700&display=swap" rel="stylesheet">
<style>
  :root {
    --pink: #e34197;
    --charcoal: #3a3a3d;
    --ink: #2b2b2e;
    --paper: #ffffff;
    --backdrop: #e9e9eb;
  }
  * { margin: 0; padding: 0; box-sizing: border-box; }
  html, body { width: 1200px; height: 900px; overflow: hidden; }
  body {
    background: var(--backdrop);
    font-family: "Montserrat", sans-serif;
    display: flex;
    flex-direction: column;
    align-items: center;
    justify-content: center;
    gap: 44px;
  }
  .card {
    position: relative;
    width: 680px;
    height: 390px;
    background: var(--paper);
    border-radius: 30px;
    overflow: hidden;
    box-shadow: 0 6px 18px rgba(0,0,0,0.12);
  }
  .card-wave { position: absolute; inset: 0; width: 100%; height: 100%; }
  .contact-list {
    position: absolute;
    top: 34px;
    left: 40px;
    list-style: none;
    font-size: 13px;
    color: var(--ink);
    line-height: 1.35;
  }
  .contact-list li { display: flex; align-items: center; gap: 9px; margin-bottom: 5px; }
  .contact-list .address { display: block; margin-bottom: 9px; font-weight: 500; }
  .contact-icon { width: 13px; height: 13px; flex: none; }
  .brand {
    position: absolute;
    display: flex;
    align-items: center;
    gap: 10px;
    color: var(--ink);
    font-weight: 700;
    letter-spacing: -0.5px;
  }
  .brand-mark { width: 14px; height: 14px; background: var(--pink); flex: none; }
  .card-front .brand { top: 118px; left: 320px; font-size: 40px; }
  .card-back .brand { top: 50%; left: 50%; transform: translate(-50%, -50%); font-size: 52px; }
  .card-back .brand-mark { width: 18px; height: 18px; }
  .holder {
    position: absolute;
    right: 58px;
    bottom: 34px;
    text-align: right;
    color: var(--paper);
  }
  .holder-name { font-size: 17px; font-weight: 500; letter-spacing: 1px; text-transform: uppercase; }
  .holder-title { font-size: 13px; margin-top: 3px; }
</style>
</head>
<body>

  <section class="card card-front">
    <svg class="card-wave" viewBox="0 0 680 390" preserveAspectRatio="none" aria-hidden="true">
      <path d="M0,170 C220,222 450,258 680,250 L680,256 C450,266 220,234 0,182 Z" fill="var(--pink)" opacity="0.45"/>
      <path d="M0,192 C220,240 460,272 680,262 L680,282 C460,290 220,262 0,214 Z" fill="var(--pink)"/>
      <path d="M0,222 C220,268 460,296 680,290 L680,390 L0,390 Z" fill="var(--charcoal)"/>
    </svg>

    <ul class="contact-list">
      <li class="address">14 Harbour Street<br>Port Macquarie NSW</li>
      <li>
        <svg class="contact-icon" viewBox="0 0 14 14"><path d="M3 1h3l1 3-2 1a8 8 0 0 0 4 4l1-2 3 1v3a1 1 0 0 1-1 1A12 12 0 0 1 2 2a1 1 0 0 1 1-1z" fill="var(--pink)"/></svg>
        02 5550 1234
      </li>
      <li>
        <svg class="contact-icon" viewBox="0 0 14 14"><rect x="3.5" y="0.5" width="7" height="13" rx="1.5" fill="var(--pink)"/><rect x="5" y="2.5" width="4" height="7" fill="#fff"/></svg>
        0455 501 234
      </li>
      <li>
        <svg class="contact-icon" viewBox="0 0 14 14"><rect x="0.5" y="2.5" width="13" height="9" rx="1" fill="var(--pink)"/><path d="M1 3l6 5 6-5" stroke="#fff" stroke-width="1.2" fill="none"/></svg>
        hello@staffcompass.au
      </li>
      <li>
        <svg class="contact-icon" viewBox="0 0 14 14"><circle cx="7" cy="7" r="6" fill="var(--pink)"/><path d="M1 7h12M7 1c-3 3-3 9 0 12M7 1c3 3 3 9 0 12" stroke="#fff" stroke-width="0.9" fill="none"/></svg>
        www.staffcompass.au
      </li>
    </ul>

    <div class="brand"><span class="brand-mark"></span>Staff Compass</div>

    <div class="holder">
      <p class="holder-name">Daniel Morrow</p>
      <p class="holder-title">Managing Director</p>
    </div>
  </section>

  <section class="card card-back">
    <div class="brand"><span class="brand-mark"></span>Staff Compass</div>
  </section>

</body>
</html>
```